Small Business Consulting Firm Needs Letterhead

We need a letterhead for our company "Brightpath Plus". Our company does outbound calling and mailing to business owner's companies who have taken high interest loans. These loans tend to put these businesses in a big financial bind short term, and we help them find better financial options. We would like the design to match our colors of our logo. Headers and footers would look nice, but we are open. We would want it to include our address, website, phone, and email info. Our address - 2000 E. Lamar Blvd. Suite 600Website - www.safeguardtoday.comEmail - info@safeguardtoday.comPhone - 855-726-1938
Industry/Entity Type
Financial Planning
Look and feel
Each slider illustrates characteristics of the customer's brand and the style your logo design should communicate.

```html
<!DOCTYPE html>
<html lang="en">
<head>
<meta charset="utf-8">
<title>Brightpath Plus Letterhead</title>
<link rel="stylesheet" href="https://fonts.googleapis.com/css2?family=Tinos&family=Arimo&family=Cousine&display=swap">
<style>
  :root {
    --bg: #e4e4e4;
    --paper: #ffffff;
    --brand-blue: #1f78bd;
    --brand-green: #6aad46;
    --ink: #2a2a2a;
    --ink-soft: #555759;
    --sig-tone: #ececec;
  }
  * { margin: 0; padding: 0; box-sizing: border-box; }
  html, body { width: 1200px; height: 1200px; overflow: hidden; }
  body { background: var(--bg); position: relative; }

  .letterhead {
    position: absolute; left: 287px; top: 160px;
    width: 626px; height: 880px;
    background: var(--paper);
    box-shadow: 0 2px 10px rgba(0,0,0,0.12);
    color: var(--ink);
  }

  .rule { position: absolute; left: 0; width: 100%; }
  .rule--top { top: 0; }
  .rule--bottom { bottom: 0; }
  .rule-main { height: 6px; background: var(--brand-blue); }
  .rule-accent { height: 2px; background: var(--brand-green); }
  .rule--top .rule-accent { margin-top: 3px; }
  .rule--bottom .rule-accent { margin-bottom: 3px; }

  .brand {
    position: absolute; top: 110px; left: 0; width: 100%;
    text-align: center; font-family: 'Tinos', serif; font-weight: 400;
    color: var(--ink-soft);
  }
  .brand-mark {
    display: block; width: 12px; height: 12px; margin: 0 auto 12px;
    background: var(--brand-blue); border-radius: 50%;
  }
  .brand-name { font-size: 26px; line-height: 1; }
  .brand-tagline { font-size: 12px; margin-top: 6px; }

  .letter-body {
    position: absolute; left: 77px; top: 232px; width: 472px;
    font-family: 'Tinos', serif; font-size: 9.6px; line-height: 12.4px;
  }
  .letter-date { margin-bottom: 13px; }
  .recipient { margin-bottom: 37px; }
  .salutation { margin-bottom: 13px; }
  .letter-body p.para { margin-bottom: 12.4px; }
  .closing { margin-top: 37px; }

  .signature {
    position: absolute; left: 77px; top: 622px; width: 60px; height: 28px;
    background: var(--sig-tone); border-radius: 4px;
  }
  .signer {
    position: absolute; left: 75px; top: 657px;
    font-family: 'Arimo', sans-serif; font-size: 14px; color: var(--ink);
  }

  .contact {
    position: absolute; left: 0; top: 756px; width: 100%;
    text-align: center; font-family: 'Cousine', monospace; font-size: 15px;
    line-height: 23.5px; color: var(--ink-soft);
  }
</style>
</head>
<body>
  <main class="letterhead">
    <div class="rule rule--top"><div class="rule-main"></div><div class="rule-accent"></div></div>

    <header class="brand">
      <span class="brand-mark"></span>
      <div class="brand-name">Brightpath Plus</div>
      <div class="brand-tagline">Consulting</div>
    </header>

    <section class="letter-body">
      <p class="letter-date">August 28, 2011</p>
      <p class="recipient">First Last Name<br>Street Address<br>City, State 00000</p>
      <p class="salutation">Dear :</p>
      <p class="para">Lorem ipsum dolor sit amet, consectetur adipiscing elit. Aenean sed augue sit amet dui tempor luctus.<br>Donec pretium neque velit.</p>
      <p class="para">Aliquam porta lectus nec mauris ornare venenatis. Vivamus non est et nisl semper convallis vel id mi,<br>&nbsp;auctor at bibendum nisl lacinia. Morbi imperdiet neque vehicula nunc convallis, in tempus velit<br>placerat. Integer consequat, est sit amet facilisis eleifend, nibh nibh varius orci, eget dictum lorem.</p>
      <p class="para">Pellentesque in magna mauris. Duis enim sapien, dictum vitae condimentum a, pulvinar vel lacus. Mauris<br>nibh. Vestibulum vitae nulla at metus elementum porta sit amet interdum elit. Nulla sollicitudin neque eu nunc<br>volutpat congue.</p>
      <p class="para">Etiam pellentesque, velit id dapibus fermentum, turpis sapien ornare dui, ac tincidunt ligula odio congue purus. Nunc<br>sed ante dui, in porta lectus. Cras nec sem lorem. In hac habitasse platea dictumst. Maecenas id diam quis dui porta<br>tristique. Sed id egestas felis. Donec ullamcorper mattis posuere. Phasellus fermentum eleifend tortor vel dapibus.<br>Vestibulum ante ipsum.</p>
      <p class="closing">Sincerely,</p>
    </section>

    <div class="signature" role="img" aria-label="Handwritten signature"></div>
    <p class="signer">Marcus Ellery</p>

    <footer class="contact">
      <div>4170 W. Corwin Ave. Suite 310</div>
      <div>855-726-1938</div>
      <div>www.brightpathplus.com</div>
      <div>info@brightpathplus.com</div>
    </footer>

    <div class="rule rule--bottom"><div class="rule-accent"></div><div class="rule-main"></div></div>
  </main>
</body>
</html>
```